Ward Compass Business Card Design*

We need a business card design for our company Ward Compass. Our company is specialized in providing online consulting services regarding medical institutions, hospitals and doctors. We work with patients worldwide looking to choose between healthcare providers. We have a website you may use as a reference, where we list doctors and clinics worldwide. So we target Medical providers as well as patients worldwide.
Target Market(s)
Medical Providers and patients around the world
Industry/Entity Type
Medical
Contact Information for Business Card
Salwa Kettani
CEO
+90 612 348 2175
info@wardcompass.example
www.wardcompass.example
14 Annakhil 7 H.R.B. Rabat, Morocco
Requirements
Must have
- Company logo/name on one full side, personal info and smaller logo and company name on the other side.
Nice to have
- Smart and elegant design

```html
<!DOCTYPE html>
<html lang="en">
<head>
<meta charset="utf-8">
<title>Ward Compass — Business Card</title>
<link href="https://fonts.googleapis.com/css2?family=Mulish:wght@400;800&display=swap" rel="stylesheet">
<style>
  :root {
    --navy: #1a4373;
    --grey: #7f7b7c;
    --violet: #3b3a95;
    --paper: #f3f3f5;
    --white: #ffffff;
    --backdrop: #e4e1dc;
  }
  * { margin: 0; padding: 0; box-sizing: border-box; }
  html, body { width: 900px; height: 1200px; overflow: hidden; }
  body {
    background: var(--backdrop);
    font-family: "Mulish", Arial, sans-serif;
    position: relative;
  }
  .card {
    position: absolute;
    left: 70px;
    width: 760px;
    height: 447px;
    overflow: hidden;
    box-shadow: 0 4px 10px rgba(0,0,0,0.25);
  }
  .card-front { top: 130px; background: var(--paper); }
  .card-back { top: 650px; background: var(--navy); }

  .wave { position: absolute; inset: 0; width: 100%; height: 100%; }

  .person { position: absolute; left: 56px; top: 62px; }
  .person-name { font-size: 26px; letter-spacing: 0.3px; color: var(--grey); font-weight: 400; }
  .person-name strong { color: var(--navy); font-weight: 800; }
  .person-role { font-size: 18px; color: var(--grey); margin-top: 2px; }

  .brand-mark { position: absolute; right: 66px; top: 56px; text-align: center; width: 190px; }
  .brand-dot { display: block; width: 118px; height: 118px; border-radius: 50%; background: var(--navy); margin: 0 auto 14px; }
  .brand-name-small { font-size: 18px; font-weight: 800; color: var(--grey); letter-spacing: 1px; }

  .contact { position: absolute; left: 55px; top: 306px; color: var(--white); font-size: 18px; line-height: 23px; }
  .contact-lines { margin-bottom: 16px; }
  .contact-row { display: flex; align-items: center; gap: 12px; }
  .contact-row svg { width: 16px; height: 16px; fill: var(--white); flex: none; }

  .brand-lockup { position: absolute; left: 0; right: 0; top: 170px; display: flex; align-items: center; justify-content: center; gap: 26px; }
  .brand-dot-large { width: 112px; height: 112px; border-radius: 50%; background: var(--white); }
  .brand-name-large { font-size: 46px; font-weight: 800; color: var(--white); letter-spacing: 0.5px; }
  .site { position: absolute; left: 0; right: 0; bottom: 22px; text-align: center; color: var(--white); font-size: 17px; letter-spacing: 4px; }
</style>
</head>
<body>
  <section class="card card-front">
    <svg class="wave" viewBox="0 0 808 475" preserveAspectRatio="none" aria-hidden="true">
      <defs>
        <linearGradient id="violetFade" x1="0" x2="1" y1="0" y2="0">
          <stop offset="0" stop-color="#3b3a95"/>
          <stop offset="0.45" stop-color="#4b4aa3"/>
          <stop offset="1" stop-color="#f3f3f5"/>
        </linearGradient>
      </defs>
      <path d="M0,238 C150,192 300,205 450,293 C565,360 685,364 808,302" fill="none" stroke="url(#violetFade)" stroke-width="9"/>
      <path d="M0,262 C150,215 300,225 450,310 C570,375 690,380 808,320 L808,475 L0,475 Z" fill="var(--grey)"/>
      <path d="M0,250 C130,215 250,220 380,290 C520,370 660,420 808,380 L808,475 L0,475 Z" fill="var(--navy)"/>
    </svg>

    <div class="person">
      <p class="person-name"><strong>SALWA</strong> KETTANI</p>
      <p class="person-role">CEO</p>
    </div>

    <div class="brand-mark">
      <span class="brand-dot"></span>
      <p class="brand-name-small">WARD COMPASS</p>
    </div>

    <div class="contact">
      <p class="contact-lines">14 Annakhil 7 H.R.B.<br>Rabat, Morocco</p>
      <p class="contact-row">
        <svg viewBox="0 0 24 24" aria-hidden="true"><path d="M6.6 10.8a15.1 15.1 0 0 0 6.6 6.6l2.2-2.2a1 1 0 0 1 1-.25 11.4 11.4 0 0 0 3.6.57 1 1 0 0 1 1 1V20a1 1 0 0 1-1 1A17 17 0 0 1 3 4a1 1 0 0 1 1-1h3.5a1 1 0 0 1 1 1c0 1.25.2 2.45.57 3.57a1 1 0 0 1-.25 1z"/></svg>
        +90 612 348 2175
      </p>
      <p class="contact-row">
        <svg viewBox="0 0 24 24" aria-hidden="true"><path d="M2 5h20v14H2z M4 7v.4l8 5.2 8-5.2V7z" fill-rule="evenodd"/></svg>
        info@wardcompass.example
      </p>
    </div>
  </section>

  <section class="card card-back">
    <div class="brand-lockup">
      <span class="brand-dot-large"></span>
      <p class="brand-name-large">WARD COMPASS</p>
    </div>
    <p class="site">www.wardcompass.example</p>
  </section>
</body>
</html>
```